Sophisticated, clean website reflecting my feminine, playful side to sell my abstract art,

I need a website no more than 3 pages to showcase my paintings, a little about me and some contact info. I do abstracts so looking for something a little edgy, yet feminine and current.
Updates

Hi there, These are some artists websites that I Iike: Marnelvoss.com (I like how airy it is) peterwallombry.com garethpolvens.com (I like how it scrolls) I'll need a place for a photo ( a headshot-i do not have it yet so I'll need to be able to upload that later) as well as an area for my bio. Also, it's important that I will be able to upload any new photos and descriptions easily so it should be user friendly. Lastly, I like in a sunny place so would like to have this seem upbeat and playful as that is how i like to paint. thanks-I'm trying to upload my photos now -

Target Market(s)

ppl ages 35-70 who want large scale art for their homes

Industry/Entity Type

art

Coding

Coded - Design and coding required

Number of Pages Required

3 page

Colors

Designer to choose colors to be used in the design.

Requirements
Must have
• photos of my art, a place for my bio, be easy to reach me. tasteful-nothing too "in your face" -my clients are pretty high end and organized. They like clean lines
Nice to have
• sophisticated background, muted tones in the back-similar clean font throughout-no cursive
Should not have
• too many dark areas. Too many blocks of color. Too serious.

```html
<!DOCTYPE html>
<html lang="en">
<head>
<meta charset="utf-8">
<title>Clara Wendell Art</title>
<link href="https://fonts.googleapis.com/css2?family=Playfair+Display:wght@400;700&family=Lato:wght@400;700&display=swap" rel="stylesheet">
<style>
:root{
  --coral:#e8675a;
  --coral-soft:#f3a79c;
  --cream:#fcefe2;
  --paper:#f2dfc9;
  --paper-deep:#ead3b8;
  --ink:#2b2622;
  --muted:#7a6e64;
  --white:#ffffff;
  --footer:#1e1c1b;
  --star:#e8a23a;
}
*{box-sizing:border-box;margin:0;padding:0}
html,body{width:1200px;height:3548px;overflow:hidden}
body{font-family:"Lato",Arial,sans-serif;color:var(--ink);background:var(--cream);position:relative}
.canvas{position:relative;width:1200px;height:3548px;overflow:hidden}
.abs{position:absolute}
.heading{font-family:"Playfair Display",Georgia,serif;font-weight:400;color:var(--ink);letter-spacing:1px}
.btn{position:absolute;display:flex;align-items:center;justify-content:center;border-radius:24px;font-size:14px;letter-spacing:1px;font-weight:700}
.btn-solid{background:var(--coral);color:var(--white)}
.btn-outline{border:1px solid #b9aca0;color:var(--ink);background:var(--white)}
.copy{font-size:14px;line-height:24px;color:var(--muted)}

/* header */
.site-header{position:absolute;left:0;top:0;width:1200px;height:112px;background:var(--white)}
.brand{position:absolute;left:32px;top:22px;font-family:"Playfair Display",Georgia,serif;font-weight:400;color:var(--coral);line-height:1;letter-spacing:2px}
.brand .line1{font-size:34px;display:block}
.brand .line2{font-size:20px;display:block;margin-top:8px;letter-spacing:5px}
.nav{position:absolute;right:40px;top:40px;display:flex;align-items:center;gap:10px;font-size:14px;letter-spacing:1px}
.nav a{color:var(--ink);text-decoration:none;padding:8px 14px}
.nav a.active{border:1px solid var(--coral);color:var(--coral);border-radius:20px}
.nav svg{margin-left:8px}

/* hero */
.hero{position:absolute;left:0;top:112px;width:1200px;height:700px;
  background:linear-gradient(120deg,#b8552f 0%,#d69a3c 25%,#e9dcc3 45%,#6f6a88 62%,#c98a38 80%,#9a3d25 100%)}
.hero-title{position:absolute;left:250px;top:260px;font-family:"Playfair Display",Georgia,serif;font-size:64px;line-height:70px;color:var(--white);letter-spacing:2px}
.hero-text{position:absolute;left:250px;top:420px;width:440px;font-size:15px;line-height:24px;color:var(--white)}

/* paintings */
.section-title{position:absolute;width:1200px;left:0;text-align:center;font-size:52px}
.card{position:absolute;top:1032px;width:232px;text-align:center}
.card-art{height:240px;width:232px}
.stars{margin-top:14px;color:var(--star);font-size:16px;letter-spacing:3px}
.card-name{margin-top:4px;font-size:15px;letter-spacing:1px}
.card .btn{position:relative;margin:14px auto 0;width:120px;height:36px;font-size:12px}

/* about */
.about{position:absolute;left:0;top:1460px;width:1200px;height:700px;background:var(--paper)}
.about-photo{position:absolute;left:688px;top:1550px;width:420px;height:420px;border-radius:50%;border:10px solid var(--white);background:radial-gradient(circle at 50% 45%,#e2b48f,#8a6a58 70%,#5a6b78)}

/* gallery */
.gallery-art{position:absolute}

/* contact */
.contact{position:absolute;left:0;top:2790px;width:1200px;height:610px;background:var(--paper)}
.field{position:absolute;background:var(--white);font-size:12px;color:var(--muted);padding:14px 12px;letter-spacing:1px}
.contact-icon{position:absolute;width:72px;height:72px;border-radius:50%;background:var(--coral-soft);display:flex;align-items:center;justify-content:center}
.contact-text{position:absolute;width:240px;text-align:center;font-size:14px;line-height:22px;color:var(--ink)}

/* footer */
.site-footer{position:absolute;left:0;top:3400px;width:1200px;height:148px;background:var(--footer)}
.social{position:absolute;top:58px;width:36px;height:36px;border-radius:50%;border:1px solid var(--white)}
.copyright{position:absolute;left:660px;top:66px;font-size:14px;color:#ddd}
.copyright span{color:var(--coral)}
</style>
</head>
<body>
<div class="canvas">

  <header class="site-header">
    <div class="brand"><span class="line1">CLARA</span><span class="line2">WENDELL ART</span></div>
    <nav class="nav">
      <a class="active">HOME</a><a>ABOUT ME</a><a>PAINTING</a><a>GALLERY</a><a>CONTACT</a>
      <svg width="18" height="18" viewBox="0 0 18 18"><circle cx="7.5" cy="7.5" r="5.5" fill="none" stroke="#2b2622" stroke-width="2"/><line x1="11.5" y1="11.5" x2="16" y2="16" stroke="#2b2622" stroke-width="2"/></svg>
      <svg width="20" height="18" viewBox="0 0 20 18"><path d="M1 2h3l2.5 10h10l2-7H6" fill="none" stroke="#2b2622" stroke-width="2"/><circle cx="8" cy="15.5" r="1.5" fill="#2b2622"/><circle cx="15" cy="15.5" r="1.5" fill="#2b2622"/></svg>
    </nav>
  </header>

  <section class="hero" role="img" aria-label="Abstract painting in rust, ochre, cream and slate blue brush strokes">
    <h1 class="hero-title">CLARA<br>WENDELL ART</h1>
    <p class="hero-text">Sed ut perspiciatis unde omnis iste natus error sit voluptatem accusantium doloremque laudantium</p>
    <div class="btn btn-solid" style="left:250px;top:500px;width:150px;height:48px">READ MORE</div>
  </section>
  <svg class="abs" style="left:0;top:772px" width="1200" height="48" viewBox="0 0 1200 48"><path d="M0 20 L60 28 L120 16 L190 30 L260 18 L330 26 L400 14 L470 28 L540 20 L610 30 L680 16 L750 26 L820 18 L890 30 L960 20 L1030 28 L1100 16 L1160 26 L1200 20 V48 H0Z" fill="var(--cream)"/></svg>

  <h2 class="heading section-title" style="top:895px">OUR PAINTING</h2>

  <div class="card" style="left:112px"><div class="card-art" role="img" aria-label="Abstract painting in violet, cream and red" style="background:linear-gradient(135deg,#6b5a8c,#e6ddd6 50%,#b54b3a)"></div><div class="stars">★★★★★</div><div class="card-name">PRODUCT NAME</div><div class="btn btn-outline">VIEW DETAILS</div></div>
  <div class="card" style="left:360px"><div class="card-art" role="img" aria-label="Abstract painting in teal, green and red" style="background:linear-gradient(135deg,#2f6e6a,#d9e2d0 50%,#b63a2e)"></div><div class="stars">★★★★★</div><div class="card-name">PRODUCT NAME</div><div class="btn btn-solid">VIEW DETAILS</div></div>
  <div class="card" style="left:608px"><div class="card-art" role="img" aria-label="Abstract painting in cream, ochre and blue" style="background:linear-gradient(135deg,#e8dcc8,#c99a3c 50%,#5a6f99)"></div><div class="stars">★★★★★</div><div class="card-name">PRODUCT NAME</div><div class="btn btn-outline">VIEW DETAILS</div></div>
  <div class="card" style="left:856px"><div class="card-art" role="img" aria-label="Abstract painting in rose, cream and brown swirls" style="background:linear-gradient(135deg,#c98a8a,#efe3da 50%,#7a4a3a)"></div><div class="stars">★★★★★</div><div class="card-name">PRODUCT NAME</div><div class="btn btn-outline">VIEW DETAILS</div></div>

  <section class="about">
    <svg class="abs" style="left:0;top:-14px" width="1200" height="30" viewBox="0 0 1200 30"><path d="M0 14 L70 8 L140 18 L210 6 L290 16 L360 8 L440 18 L520 6 L600 16 L680 8 L760 18 L840 6 L920 16 L1000 8 L1080 18 L1150 8 L1200 14 V30 H0Z" fill="var(--paper)"/></svg>
  </section>
  <div class="abs" style="left:0;top:1620px;width:100px;height:1px;background:var(--ink)"></div>
  <h2 class="heading abs" style="left:112px;top:1588px;font-size:52px;line-height:60px">ABOUT ME</h2>
  <p class="copy abs" style="left:112px;top:1668px;width:440px">Sed ut perspiciatis unde omnis iste natus error sit voluptatem accusantium doloremque laudantium, totam rem aperiam, eaque ipsa quae ab illo inventore veritatis et quasi architecto beatae vitae dicta sunt explicabo. Nemo enim ipsam voluptatem quia voluptas sit aspernatur aut odit aut fugit, sed quia consequuntur magni dolores eos qui ratione voluptatem sequi nesciunt. Neque porro quisquam est, qui dolorem ipsum quia dolor sit amet, consectetur, adipisci velit, sed quia non numquam eius modi tempora incidunt ut labore et dolore magnam aliquam quaerat voluptatem.</p>
  <div class="btn btn-solid" style="left:112px;top:1940px;width:150px;height:48px">READ MORE</div>
  <div class="about-photo" role="img" aria-label="Portrait of the artist holding a palette in her studio"></div>
  <svg class="abs" style="left:0;top:2140px" width="1200" height="30" viewBox="0 0 1200 30"><path d="M0 0 H1200 V12 L1130 20 L1050 8 L970 18 L890 6 L810 16 L730 8 L650 20 L570 8 L490 18 L410 6 L330 16 L250 8 L170 20 L90 8 L0 16Z" fill="var(--paper)"/></svg>

  <div class="gallery-art" role="img" aria-label="Abstract painting in red and cream" style="left:112px;top:2224px;width:186px;height:240px;background:linear-gradient(135deg,#f0e6dc,#b8402f 60%,#6a2a22)"></div>
  <div class="gallery-art" role="img" aria-label="Abstract painting in teal and white" style="left:318px;top:2180px;width:186px;height:240px;background:linear-gradient(160deg,#2f7f86,#d8e0dc 55%,#1e3e48)"></div>
  <div class="gallery-art" role="img" aria-label="Abstract painting in yellow, blue and cream" style="left:518px;top:2224px;width:186px;height:250px;background:linear-gradient(135deg,#e3c24a,#f2ead8 50%,#4a6a99)"></div>
  <div class="gallery-art" role="img" aria-label="Abstract painting in red, green and white" style="left:112px;top:2490px;width:186px;height:250px;background:linear-gradient(135deg,#c23b2e,#f1ebe2 50%,#3b7a4a)"></div>
  <div class="gallery-art" role="img" aria-label="Abstract painting in teal and cream swirls" style="left:318px;top:2440px;width:186px;height:250px;background:linear-gradient(135deg,#3a8a8a,#eadfcf 50%,#7a3a4a)"></div>
  <div class="gallery-art" role="img" aria-label="Abstract painting in rose and violet" style="left:518px;top:2496px;width:120px;height:150px;background:linear-gradient(135deg,#d7a3b8,#f4ece6 50%,#7a5a8c)"></div>

  <h2 class="heading abs" style="left:752px;top:2256px;font-size:52px;line-height:60px">OUR GALLERY</h2>
  <p class="copy abs" style="left:752px;top:2336px;width:360px">Sed ut perspiciatis unde omnis iste natus error sit voluptatem accusantium doloremque laudantium, totam rem aperiam, eaque ipsa quae ab illo inventore veritatis et quasi architecto beatae vitae dicta sunt explicabo. Nemo enim ipsam voluptatem quia voluptas sit aspernatur aut odit aut fugit, sed quia consequuntur magni dolores eos qui ratione voluptatem sequi nesciunt.</p>
  <div class="btn btn-outline" style="left:752px;top:2568px;width:150px;height:48px">READ MORE</div>

  <section class="contact">
    <svg class="abs" style="left:0;top:-14px" width="1200" height="30" viewBox="0 0 1200 30"><path d="M0 12 L80 20 L160 6 L240 16 L320 8 L400 20 L480 6 L560 16 L640 8 L720 18 L800 6 L880 16 L960 8 L1040 20 L1120 8 L1200 16 V30 H0Z" fill="var(--paper)"/></svg>
  </section>
  <h2 class="heading section-title" style="top:2840px">CONTACT US</h2>
  <div class="field" style="left:300px;top:2950px;width:292px;height:44px">FIRST NAME :</div>
  <div class="field" style="left:608px;top:2950px;width:292px;height:44px">LAST NAME :</div>
  <div class="field" style="left:300px;top:3006px;width:292px;height:44px">EMAIL :</div>
  <div class="field" style="left:608px;top:3006px;width:292px;height:44px">PHONE :</div>
  <div class="field" style="left:300px;top:3062px;width:600px;height:100px">MESSAGE :</div>
  <div class="btn btn-solid" style="left:525px;top:3140px;width:150px;height:48px">SUBMIT</div>

  <div class="contact-icon" style="left:316px;top:3226px"><svg width="26" height="30" viewBox="0 0 26 30"><path d="M13 2a10 10 0 0 1 10 10c0 7-10 16-10 16S3 19 3 12A10 10 0 0 1 13 2z" fill="#fff"/><circle cx="13" cy="12" r="4" fill="var(--coral-soft)"/></svg></div>
  <div class="contact-icon" style="left:572px;top:3226px"><svg width="26" height="26" viewBox="0 0 26 26"><path d="M6 2l5 5-3 3c2 4 4 6 8 8l3-3 5 5-3 4C11 24 2 15 2 5z" fill="#fff"/></svg></div>
  <div class="contact-icon" style="left:816px;top:3226px"><svg width="28" height="20" viewBox="0 0 28 20"><rect x="1" y="1" width="26" height="18" fill="#fff"/><path d="M1 1l13 10L27 1" fill="none" stroke="var(--coral-soft)" stroke-width="2"/></svg></div>
  <div class="contact-text" style="left:232px;top:3312px">P.O Box Lorem Ipsum Dummy<br>Lorem 145</div>
  <div class="contact-text" style="left:488px;top:3312px">+1 888 888 8888</div>
  <div class="contact-text" style="left:732px;top:3312px">info@clarawendellart.com</div>

  <footer class="site-footer">
    <div class="social" style="left:112px"></div>
    <div class="social" style="left:156px"></div>
    <div class="social" style="left:200px"></div>
    <div class="social" style="left:244px"></div>
    <div class="social" style="left:288px"></div>
    <p class="copyright">© Copyright 2017 <span>Clara Wendell Art</span>. All Rights Reserved.</p>
  </footer>

</div>
</body>
</html>
```